Business card design needed

I need a business card design for a dog walking, dog minding and dog training business. Please refer to my website for the basic company colours and fonts I'm after. Planning on a double sided card, so all information doesn't need to be on the 'front' side.
Cheers

Industry/Entity Type

Dog Training

Contact Information for Business Card

Bramble Paws - gathering hounds
Rua 0498376214
bramblepaws.com.au
-walking
-holiday stays
-onsite care
-training and behavioural consultations

```html
<!DOCTYPE html>
<html lang="en">
<head>
<meta charset="utf-8">
<title>Bramble Paws – business card</title>
<link rel="stylesheet" href="https://fonts.googleapis.com/css2?family=Exo+2:ital,wght@0,300;0,400;0,600;1,300&display=swap">
<style>
  :root {
    --card-grey: #5a5b5d;
    --accent-orange: #e2582a;
    --ink-white: #ffffff;
    --art-light: #6a6b6e;
    --art-dark: #535456;
  }
  * { margin: 0; padding: 0; box-sizing: border-box; }
  html, body {
    width: 1200px;
    height: 692px;
    overflow: hidden;
    background: var(--card-grey);
  }
  .card {
    position: relative;
    width: 1200px;
    height: 692px;
    background: var(--card-grey);
    font-family: "Exo 2", sans-serif;
    color: var(--ink-white);
  }
  .contact {
    position: absolute;
    right: 48px;
    top: 82px;
    text-align: right;
  }
  .contact__line {
    font-size: 60px;
    font-weight: 300;
    line-height: 1;
    letter-spacing: 0.5px;
  }
  .contact__name { font-weight: 600; }
  .contact__area {
    margin-top: 28px;
    font-size: 35px;
    font-weight: 300;
    font-style: italic;
    line-height: 1;
  }
  .dog-art {
    position: absolute;
    left: 0;
    top: 282px;
    width: 390px;
    height: 370px;
    background: linear-gradient(160deg, var(--art-light), var(--art-dark));
    border-radius: 6px;
  }
  .brand {
    position: absolute;
    left: 322px;
    top: 462px;
  }
  .brand__name {
    font-size: 116px;
    font-weight: 300;
    line-height: 1;
    color: var(--accent-orange);
    letter-spacing: 1px;
    white-space: nowrap;
  }
  .brand__tagline {
    margin-top: 10px;
    margin-left: 6px;
    font-size: 48px;
    font-weight: 300;
    line-height: 1;
    color: var(--ink-white);
  }
</style>
</head>
<body>
  <main class="card">
    <div class="contact">
      <p class="contact__line"><span class="contact__name">Rua</span> 0498 376 214</p>
      <p class="contact__area">servicing the inner suburbs of Melbourne</p>
    </div>

    <div class="dog-art" role="img" aria-label="Line illustration of a standing dog wearing an orange collar, with an orange leash trailing off to the left"></div>

    <div class="brand">
      <p class="brand__name">BRAMBLE PAWS</p>
      <p class="brand__tagline">gathering hounds</p>
    </div>
  </main>
</body>
</html>
```